Web portal for events

The project is about creating a web application - portal for culture events in Denmark.

Design

We aim for very simplistic, light and fully responsive design. The white background is preferable, as well as light color tones. As inspirational points we like the colors used in www.parvolio.com and www.brindlemoor.org

FORMAT AND REQUIREMENTS:
1. Design should be provided based on the wireframes specified as a link below.
2. The design (and all of its pages) should be provided in three resolution variants:
- Desktop
- Tablet
- Phone
3. The design should be provided as PSD, where each page/section should be in its own PSD file
4. All graphical elements in the design should be delivered as single layers which can then be extracted from the PSD.
5. All graphical elements (icons, graphical buttons, etc.) should be provided as vector objects in the PSD, so that they can be exported into different sizes without loss of quality (for responsiveness)
6. The design should use either web safe fonts or Google Fonts.

RESPONSIVENESS
The web application should be visible on any devices (i.e. responsive design)

WIREFRAMES:
https://velkotrams.examplewire.com/projects/fennoplex/prototype/Homepage?key=3b7c19d0f2a84e6c5d1e9a07b4f2c8d6e1a3f590

We expect design of the following wireframes:

Homepage:
https://velkotrams.examplewire.com/projects/fennoplex/Homepage

For arrangører - billede uploaded:
https://velkotrams.examplewire.com/projects/fennoplex/For%20arrang%C3%B8rer%20-%20billede%20uploaded

Further specifications of the project (i.e. functionality, etc.):
https://files.quorvane.net/document/d/8pKw_Rt2mZqLx4NvB7yHc0aEs9uGdJf3TiOb6nVlW1k/edit?usp=sharing

```html
<!DOCTYPE html>
<html lang="da">
<head>
<meta charset="utf-8">
<title>KULTRA – Din guide till kultur or events</title>
<link rel="stylesheet" href="https://fonts.googleapis.com/css2?family=Ubuntu:wght@400;500&display=swap">
<style>
:root{
  --red:#f2330f;
  --red-dark:#dc2c0b;
  --red-deep:#b8260a;
  --red-soft:#fb5a36;
  --line-red:#ef5a3a;
  --ink:#444;
  --muted:#777;
  --light:#f4f4f4;
  --rule:#e3e3e3;
  --white:#fff;
  --dark:#2e2e2e;
}
*{box-sizing:border-box;margin:0;padding:0}
html,body{width:1108px;height:1200px;overflow:hidden;background:var(--white);font-family:"Ubuntu",sans-serif;color:var(--ink)}
.canvas{position:relative;width:1108px;height:1200px}
.abs{position:absolute}

/* header */
.site-header{position:absolute;left:0;top:0;width:1108px;height:100px;background:var(--red)}
.brand{position:absolute;left:145px;top:20px;color:var(--white)}
.brand-name{font-size:44px;font-weight:500;letter-spacing:1px;line-height:48px}
.brand-tag{font-size:11.5px;margin-top:4px}
.search{position:absolute;left:385px;top:48px;width:313px;height:27px;border-radius:14px;background:var(--red-soft);color:#fde;font-size:11px;line-height:27px;padding-left:15px}
.search svg{position:absolute;right:10px;top:5px}
.pill-btn{position:absolute;top:48px;height:27px;border-radius:14px;background:var(--red-deep);color:var(--white);font-size:12px;line-height:27px;text-align:center}
.login{position:absolute;left:832px;top:-6px;width:134px;height:33px;border-radius:0 0 16px 16px;border-radius:16px;background:var(--white);color:#555;font-size:12px;text-align:center;padding-top:12px}

/* nav */
.main-nav{position:absolute;left:0;top:100px;width:1108px;height:49px;background:var(--red-dark)}
.nav-item{position:absolute;top:0;height:49px;line-height:49px;color:var(--white);font-size:15px;transform:translateX(-50%)}
.nav-div{position:absolute;top:1px;width:1px;height:48px;background:var(--line-red)}

/* listing */
.list-head{position:absolute;left:138px;top:181px;width:832px;height:44px;background:var(--light);border-top:1px solid var(--rule);border-bottom:1px solid var(--rule)}
.section-title{position:absolute;font-size:17px;color:#666;font-weight:400}
.sort-label{position:absolute;left:189px;top:18px;font-size:9.5px;color:#555}
.sort-box{position:absolute;top:12px;height:21px;background:var(--white);border:1px solid #d8d8d8;font-size:9.5px;color:#666;line-height:19px;padding-left:8px}
.col-divider{position:absolute;left:748px;top:181px;width:1px;height:830px;background:var(--rule)}

.card{position:absolute;width:180px}
.card-img{width:180px;height:92px}
.card-title{font-size:14px;color:#444;margin-top:17px}
.card-meta{display:flex;justify-content:space-between;font-size:9.5px;margin-top:5px;color:var(--muted)}
.card-meta .date{color:var(--red);padding-right:8px}
.card-actions{display:flex;gap:5px;margin-top:9px}
.btn-primary{width:73px;height:27px;background:var(--red);color:var(--white);border-radius:2px;font-size:11px;text-align:center;line-height:27px}
.btn-ghost{width:101px;height:27px;background:#f3f3f3;border:1px solid #d6d6d6;border-radius:2px;color:#555;font-size:11px;text-align:center;line-height:25px}

.pager a{position:absolute;top:1046px;width:25px;height:23px;border:1px solid #ccc;font-size:11px;line-height:21px;text-align:center;color:#555;text-decoration:none}
.pager a.current{background:#eee;border-color:#eee}

/* sidebar */
.fav{position:absolute;left:771px;width:200px}
.fav-img{position:absolute;left:0;top:0;width:84px;height:62px}
.fav-name{position:absolute;left:91px;top:1px;font-size:12px;color:#444}
.fav-text{position:absolute;left:91px;top:19px;width:110px;font-size:9px;line-height:14.5px;color:var(--muted)}
.side-rule{position:absolute;left:770px;width:200px;height:1px;background:var(--rule)}
.email{position:absolute;left:771px;top:646px;width:193px;height:27px;border:1px solid #ccc;background:#f6f6f6;font-size:9px;color:#555;line-height:25px;padding-left:9px}
.subscribe{position:absolute;left:772px;top:682px;width:94px;height:25px;background:var(--dark);color:var(--white);font-size:11px;line-height:25px;text-align:center;border-radius:2px}

/* footer */
.site-footer{position:absolute;left:0;top:1098px;width:1108px;height:102px;background:#f7f7f7;border-top:1px solid #ddd}
.foot-links{position:absolute;left:138px;top:32px;font-size:11.5px;color:#555;word-spacing:2px}
.copy{position:absolute;left:138px;top:56px;font-size:9.5px;color:#888}
</style>
</head>
<body>
<div class="canvas">

<header class="site-header">
  <div class="brand"><div class="brand-name">KULTRA</div><div class="brand-tag">Din guide till kultur or events</div></div>
  <div class="search">Search here
    <svg width="18" height="18" viewBox="0 0 18 18"><circle cx="7.5" cy="7.5" r="6" fill="none" stroke="#fff" stroke-width="2"/><line x1="12" y1="12" x2="16.5" y2="16.5" stroke="#fff" stroke-width="2.2" stroke-linecap="round"/></svg>
  </div>
  <div class="pill-btn" style="left:709px;width:84px">SOG</div>
  <div class="pill-btn" style="left:797px;width:127px">Avancret soging</div>
  <div class="login">Login &nbsp;/&nbsp; Sign Up</div>
</header>

<nav class="main-nav">
  <span class="nav-item" style="left:185px">ALLE</span>
  <span class="nav-div" style="left:221px"></span>
  <span class="nav-item" style="left:262px">MUSIK</span>
  <span class="nav-div" style="left:302px"></span>
  <span class="nav-item" style="left:344px">SPORT</span>
  <span class="nav-div" style="left:385px"></span>
  <span class="nav-item" style="left:433px">TEATER</span>
  <span class="nav-div" style="left:478px"></span>
  <span class="nav-item" style="left:539px">UDSTILLING</span>
  <span class="nav-div" style="left:600px"></span>
  <span class="nav-item" style="left:646px">AELDRE</span>
  <span class="nav-div" style="left:690px"></span>
  <span class="nav-item" style="left:731px">BORN</span>
  <span class="nav-div" style="left:770px"></span>
  <span class="nav-item" style="left:818px">MOTION</span>
  <span class="nav-div" style="left:866px"></span>
  <span class="nav-item" style="left:915px">DIVERSE</span>
</nav>

<div class="list-head">
  <h2 class="section-title" style="left:17px;top:12px">POPULAR EVENTS</h2>
  <span class="sort-label">Sort By:</span>
  <span class="sort-box" style="left:239px;width:61px">Pouplar</span>
  <span class="sort-box" style="left:311px;width:79px">Omrdde
    <svg class="abs" style="right:6px;top:7px" width="7" height="5" viewBox="0 0 7 5"><path d="M0 0h7L3.5 5z" fill="#444"/></svg></span>
  <span class="sort-box" style="left:397px;width:50px">Date</span>
  <span class="sort-box" style="left:455px;width:50px">Pris</span>
  <h2 class="section-title" style="left:633px;top:12px">MINE FAVORITTER</h2>
</div>
<div class="col-divider"></div>

<!-- row 1 -->
<article class="card" style="left:138px;top:242px"><div class="card-img" role="img" aria-label="Photo of guests mingling at a reception" style="background:linear-gradient(135deg,#5a4a3e,#c9b8a6)"></div><h3 class="card-title">Etiam nunc venenatis</h3><div class="card-meta"><span>Sed odio auctor</span><span class="date">June, 20, 2014</span></div><div class="card-actions"><span class="btn-primary">Se Event</span><span class="btn-ghost">Best Favourite</span></div></article>
<article class="card" style="left:341px;top:242px"><div class="card-img" role="img" aria-label="Photo of a speaker addressing a seated audience" style="background:linear-gradient(135deg,#c8bfb2,#8a8c96)"></div><h3 class="card-title">Etiam nunc venenatis</h3><div class="card-meta"><span>Sed odio auctor</span><span class="date">June, 20, 2014</span></div><div class="card-actions"><span class="btn-primary">Se Event</span><span class="btn-ghost">Best Favourite</span></div></article>
<article class="card" style="left:543px;top:242px"><div class="card-img" role="img" aria-label="Photo of a host at a formal event" style="background:linear-gradient(135deg,#8a6a2e,#3a3530)"></div><h3 class="card-title">Etiam nunc venenatis</h3><div class="card-meta"><span>Sed odio auctor</span><span class="date">June, 20, 2014</span></div><div class="card-actions"><span class="btn-primary">Se Event</span><span class="btn-ghost">Best Favourite</span></div></article>

<!-- row 2 -->
<article class="card" style="left:138px;top:447px"><div class="card-img" role="img" aria-label="Photo of an empty conference hall" style="background:linear-gradient(135deg,#d7d4cd,#4a505a)"></div><h3 class="card-title">Etiam nunc venenatis</h3><div class="card-meta"><span>Sed odio auctor</span><span class="date">June, 20, 2014</span></div><div class="card-actions"><span class="btn-primary">Se Event</span><span class="btn-ghost">Best Favourite</span></div></article>
<article class="card" style="left:341px;top:447px"><div class="card-img" role="img" aria-label="Photo of an audience applauding at a seminar" style="background:linear-gradient(135deg,#bfc3c6,#55595e)"></div><h3 class="card-title">Etiam nunc venenatis</h3><div class="card-meta"><span>Sed odio auctor</span><span class="date">June, 20, 2014</span></div><div class="card-actions"><span class="btn-primary">Se Event</span><span class="btn-ghost">Best Favourite</span></div></article>
<article class="card" style="left:543px;top:447px"><div class="card-img" role="img" aria-label="Photo of a conference attendee in a suit" style="background:linear-gradient(135deg,#2e3440,#8d9198)"></div><h3 class="card-title">Etiam nunc venenatis</h3><div class="card-meta"><span>Sed odio auctor</span><span class="date">June, 20, 2014</span></div><div class="card-actions"><span class="btn-primary">Se Event</span><span class="btn-ghost">Best Favourite</span></div></article>

<!-- row 3 -->
<article class="card" style="left:138px;top:641px"><div class="card-img" role="img" aria-label="Photo of guests at a buffet reception" style="background:linear-gradient(135deg,#c9b6a4,#a0522d)"></div><h3 class="card-title">Etiam nunc venenatis</h3><div class="card-meta"><span>Sed odio auctor</span><span class="date">June, 20, 2014</span></div><div class="card-actions"><span class="btn-primary">Se Event</span><span class="btn-ghost">Best Favourite</span></div></article>
<article class="card" style="left:341px;top:641px"><div class="card-img" role="img" aria-label="Photo of colleagues networking over coffee" style="background:linear-gradient(135deg,#4a5260,#c4c0bb)"></div><h3 class="card-title">Etiam nunc venenatis</h3><div class="card-meta"><span>Sed odio auctor</span><span class="date">June, 20, 2014</span></div><div class="card-actions"><span class="btn-primary">Se Event</span><span class="btn-ghost">Best Favourite</span></div></article>
<article class="card" style="left:543px;top:641px"><div class="card-img" role="img" aria-label="Photo of a set banquet table with wine" style="background:linear-gradient(135deg,#efe6dc,#b49a9c)"></div><h3 class="card-title">Etiam nunc venenatis</h3><div class="card-meta"><span>Sed odio auctor</span><span class="date">June, 20, 2014</span></div><div class="card-actions"><span class="btn-primary">Se Event</span><span class="btn-ghost">Best Favourite</span></div></article>

<!-- row 4 -->
<article class="card" style="left:138px;top:846px"><div class="card-img" role="img" aria-label="Photo of friends toasting at dinner" style="background:linear-gradient(135deg,#3e3a36,#9c7c66)"></div><h3 class="card-title">Etiam nunc venenatis</h3><div class="card-meta"><span>Sed odio auctor</span><span class="date">June, 20, 2014</span></div><div class="card-actions"><span class="btn-primary">Se Event</span><span class="btn-ghost">Best Favourite</span></div></article>
<article class="card" style="left:341px;top:846px"><div class="card-img" role="img" aria-label="Photo of a concert crowd under stage lights" style="background:radial-gradient(circle at 50% 40%,#f6c98a,#6b3a18 45%,#1a1210)"></div><h3 class="card-title">Etiam nunc venenatis</h3><div class="card-meta"><span>Sed odio auctor</span><span class="date">June, 20, 2014</span></div><div class="card-actions"><span class="btn-primary">Se Event</span><span class="btn-ghost">Best Favourite</span></div></article>
<article class="card" style="left:543px;top:846px"><div class="card-img" role="img" aria-label="Photo of a lively party toast" style="background:linear-gradient(135deg,#2c3a5a,#9a4a3a)"></div><h3 class="card-title">Etiam nunc venenatis</h3><div class="card-meta"><span>Sed odio auctor</span><span class="date">June, 20, 2014</span></div><div class="card-actions"><span class="btn-primary">Se Event</span><span class="btn-ghost">Best Favourite</span></div></article>

<nav class="pager">
  <a class="current" style="left:380px">1</a>
  <a style="left:413px">2</a>
  <a style="left:445px">3</a>
</nav>

<!-- sidebar -->
<aside>
  <div class="fav" style="top:242px"><div class="fav-img" role="img" aria-label="Photo of a performer on the red carpet" style="background:linear-gradient(135deg,#d9dde2,#4a4e55)"></div><div class="fav-name">Event Name</div><p class="fav-text">Etiam est nunc venena-tis in tristique eu imperdiet ac</p></div>
  <div class="side-rule" style="top:317px"></div>
  <div class="fav" style="top:329px"><div class="fav-img" role="img" aria-label="Photo of a concert stage with spotlights" style="background:radial-gradient(circle at 50% 35%,#f0f0f0,#4a5a55 45%,#111)"></div><div class="fav-name">Event Name</div><p class="fav-text">Etiam est nunc venena-tis in tristique eu imperdiet ac</p></div>
  <div class="side-rule" style="top:406px"></div>
  <div class="fav" style="top:419px"><div class="fav-img" role="img" aria-label="Photo of guests arriving on a red carpet" style="background:linear-gradient(135deg,#3a4a7a,#b8262a)"></div><div class="fav-name">Event Name</div><p class="fav-text">Etiam est nunc venena-tis in tristique eu imperdiet ac</p></div>
  <span class="btn-ghost abs" style="left:771px;top:501px;width:120px;height:27px">See More Favorite</span>
  <div class="side-rule" style="top:550px"></div>
  <h2 class="section-title" style="left:770px;top:572px;font-size:18px">NYHEDSBREV</h2>
  <p class="abs" style="left:771px;top:598px;width:200px;font-size:10px;line-height:14.5px;color:var(--muted)">Suspendisse vulputate aliquam dui Nulla elementum dui ut augue Aliquam vehicula mi at mauris</p>
  <div class="email">email address</div>
  <div class="subscribe">SUBSCRIBE</div>
</aside>

<footer class="site-footer">
  <div class="foot-links">Om Kultra &nbsp;| &nbsp;Vikar &amp; Betingelser &nbsp;| &nbsp;Kobspolitk &nbsp;| &nbsp;Nyhedsbrev &nbsp;| &nbsp;kontact &nbsp;| &nbsp;Login/Register &nbsp;| &nbsp;Help &nbsp;| &nbsp;For arrangrer &nbsp;| &nbsp;For Kommuner or</div>
  <div class="copy">© 2014 Company Name &nbsp;All right reserved &nbsp;Term of Use</div>
</footer>

</div>
</body>
</html>
```